Business Cards for a law firm

Business cards for our law firm. Use our silhoette logo and OAK PARTNERS - check our website (www.oakpartners.example)

Contact Information for Business Card

our silhouette logo, OAK PARTNERS, 800-555-0147, Dorian Pemberton, dorian@oakpartners.example

Requirements
Must have
• our silhouette logo, OAK PARTNERS, 800-555-0147, Dorian Pemberton, dorian@oakpartners.example

```html
<!DOCTYPE html>
<html lang="en">
<head>
<meta charset="utf-8">
<title>Oak Partners – Business Cards</title>
<link rel="stylesheet" href="https://fonts.googleapis.com/css2?family=Tenor+Sans&family=Montserrat:wght@700&display=swap">
<style>
  :root {
    --navy: #24346b;
    --paper: #f0f0f0;
    --backdrop: #e4e7e9;
    --white: #ffffff;
    --navy-soft: #5a6894;
  }
  * { margin: 0; padding: 0; box-sizing: border-box; }
  html, body {
    width: 1200px; height: 960px; overflow: hidden;
    background: var(--backdrop);
  }
  .canvas { position: relative; width: 1200px; height: 960px; }
  .card {
    position: absolute; left: 249px; width: 702px; height: 400px; overflow: hidden;
    font-family: "Tenor Sans", sans-serif;
  }
  .card--front { top: 60px; background: var(--navy); }
  .card--back { top: 500px; background: var(--paper); }

  .front-wordmark {
    position: absolute; left: 170px; top: 140px;
    color: var(--white); font-size: 54px; line-height: 46px; letter-spacing: 1px;
  }

  .partners-figure {
    position: absolute; left: 0; top: 0; width: 276px; height: 400px;
    background: linear-gradient(90deg, var(--navy) 0 56px, var(--navy-soft) 56px, var(--navy) 100%);
  }

  .back-wordmark {
    position: absolute; right: 27px; top: 38px;
    color: var(--navy); font-size: 30px; letter-spacing: 1px; white-space: nowrap;
  }

  .holder-name {
    position: absolute; right: 31px; top: 244px;
    color: var(--navy); font-size: 31px; white-space: nowrap; letter-spacing: 0.5px;
  }
  .holder-name .given { font-family: "Montserrat", sans-serif; font-weight: 700; letter-spacing: 1px; }
  .name-marker {
    position: absolute; right: 0; top: 246px; width: 13px; height: 30px; background: var(--navy);
  }

  .contact-list {
    position: absolute; right: 26px; top: 306px; list-style: none;
    color: var(--navy); text-align: right;
  }
  .contact-list li {
    display: flex; justify-content: flex-end; align-items: center; gap: 12px;
    height: 23px; letter-spacing: 1px;
  }
  .contact-list .phone { font-size: 20px; }
  .contact-list .web, .contact-list .email { font-size: 16px; }
  .contact-list svg { width: 15px; height: 15px; flex: none; }
</style>
</head>
<body>
<main class="canvas">
  <section class="card card--front" aria-label="Card front">
    <div class="front-wordmark">OAK<br>PARTNERS</div>
  </section>

  <section class="card card--back" aria-label="Card back">
    <div class="partners-figure" role="img" aria-label="Silhouettes of two partners in suits standing side by side"></div>
    <div class="back-wordmark">OAK PARTNERS</div>

    <p class="holder-name"><span class="given">DORIAN</span> PEMBERTON</p>
    <span class="name-marker"></span>

    <ul class="contact-list">
      <li class="phone">800-555-0147
        <svg viewBox="0 0 24 24" aria-hidden="true"><path fill="var(--navy)" d="M6.6 10.8a15 15 0 0 0 6.6 6.6l2.2-2.2a1 1 0 0 1 1-.25 11.4 11.4 0 0 0 3.6.57 1 1 0 0 1 1 1V20a1 1 0 0 1-1 1A17 17 0 0 1 3 4a1 1 0 0 1 1-1h3.5a1 1 0 0 1 1 1c0 1.25.2 2.45.57 3.57a1 1 0 0 1-.25 1z"/></svg>
      </li>
      <li class="web">WWW.OAKPARTNERS.EXAMPLE
        <svg viewBox="0 0 24 24" aria-hidden="true"><circle cx="12" cy="12" r="10" fill="none" stroke="var(--navy)" stroke-width="2"/><path d="M2 12h20M12 2c3 3 3 17 0 20M12 2c-3 3-3 17 0 20" fill="none" stroke="var(--navy)" stroke-width="1.6"/></svg>
      </li>
      <li class="email">DORIAN@OAKPARTNERS.EXAMPLE
        <svg viewBox="0 0 24 24" aria-hidden="true"><rect x="2" y="5" width="20" height="15" fill="none" stroke="var(--navy)" stroke-width="2"/><path d="M2 6l10 8 10-8" fill="none" stroke="var(--navy)" stroke-width="2"/></svg>
      </li>
    </ul>
  </section>
</main>
</body>
</html>
```